Corporate brochure design 4 pages

Hi,

We are a real estate company based in Europe.

We have almost finalized a rebranding.

We are developing a brand book guidelines (still on working process) to help you undertstand the look and feel of our new CI. I would like to receive proposals of design for a corporate brochure template. I need to receive the Indesign files with full ownership rights to be able to adapt all our documentation with this template.
Regarding the images, you can take gabaris on www.pelvarimages.example. I will be able to take them afterwards.

There will be 4 pages. you will receive the 4 pages on pdf for your consideration with our (almost) actual layout.

- 1st page: cover
- 2nd page: company presentation in french and english
- 3rd page: some market data + graph
- 4th page: 2 retail centers presentation.

In the template, i need to have:
- the paragraph styles in order
- 2 different masters with top/bottom/page number aso.

Please feel free to ask any other questions.

best regards,
Updates

I would like to precise tha t we are active on the commercial real estate sector:

- office transactions (rent /sales)
- property management of administrative and business buildings
- Valuation of properties
- Capital markets (investment advices for selling building)

Industry/Entity Type

Real Estate

Colors

Designer to choose colors to be used in the design.

```html
<!DOCTYPE html>
<html lang="en">
<head>
<meta charset="utf-8">
<title>Brixell – Luxembourg Office Market Report Q3-2013</title>
<link href="https://fonts.googleapis.com/css2?family=Arimo:wght@400;700&display=swap" rel="stylesheet">
<style>
  :root {
    --brand-orange: #f26a24;
    --ink: #111111;
    --tagline-grey: #2f2f2f;
    --white: #ffffff;
    --sky-top: #dfe7ee;
    --sky-mid: #9fb4c6;
    --tower-blue: #5f7f98;
    --deep-shadow: #1e2530;
  }
  * { margin: 0; padding: 0; box-sizing: border-box; }
  html, body { width: 848px; height: 1200px; overflow: hidden; background: var(--white); }
  body { font-family: "Arimo", Arial, sans-serif; }

  .cover { position: relative; width: 848px; height: 1200px; overflow: hidden; }

  .cover-photo {
    position: absolute; left: 0; top: 240px; width: 848px; height: 960px;
    background:
      radial-gradient(ellipse 420px 180px at 380px 720px, rgba(198,150,120,0.55), transparent 70%),
      linear-gradient(180deg, var(--sky-top) 0%, var(--sky-mid) 30%, var(--tower-blue) 60%, var(--deep-shadow) 100%);
  }

  .brand-band {
    position: absolute; left: 0; top: 0; width: 848px; height: 240px;
    background: var(--brand-orange);
  }
  .brand-name {
    position: absolute; right: 88px; top: 160px;
    font-weight: 400; font-size: 72px; line-height: 72px;
    color: var(--white);
  }
  .brand-tagline {
    position: absolute; right: 88px; top: 252px;
    font-weight: 400; font-size: 20px; letter-spacing: 1px;
    color: var(--tagline-grey);
  }

  .report-title {
    position: absolute; left: 0; top: 408px; width: 848px;
    text-align: center; color: var(--ink); font-weight: 400;
  }
  .report-title span { display: block; }
  .report-place { font-size: 70px; line-height: 78px; font-weight: 400; }
  .report-name { font-size: 72px; line-height: 82px; font-weight: 700; letter-spacing: -0.5px; }
  .report-period { font-size: 68px; line-height: 82px; font-weight: 400; }

  .services-box {
    position: absolute; left: 553px; top: 976px; width: 295px; height: 164px;
    background: var(--brand-orange); color: var(--white);
    padding: 14px 6px 0 10px;
  }
  .services-list { list-style: none; font-weight: 700; font-size: 15px; line-height: 18.5px; }
  .services-list li { padding-left: 10px; text-indent: -10px; }
  .services-list li::before { content: "- "; }
  .services-note { font-size: 11.5px; line-height: 15px; white-space: nowrap; }
</style>
</head>
<body>
  <main class="cover">
    <div class="cover-photo" role="img" aria-label="Glass office towers against a blue sky with two business people shaking hands in the foreground"></div>

    <header class="brand-band"></header>
    <div class="brand-name">Brixell</div>
    <div class="brand-tagline">Commercial Real Estate</div>

    <h1 class="report-title">
      <span class="report-place">Luxembourg</span>
      <span class="report-name">Office Market Report</span>
      <span class="report-period">Q3-2013</span>
    </h1>

    <aside class="services-box">
      <ul class="services-list">
        <li>Office Transactions (rent /sales)</li>
        <li>Property Management of<br>Administrative and<br>Business Buildings</li>
        <li>Valuation of properties</li>
        <li>Capital Markets</li>
      </ul>
      <p class="services-note">(investment advices for selling building)</p>
    </aside>
  </main>
</body>
</html>
```